Website re-design for Brightmoor LLC website ( has existing website )

Looking to do a complete re-design of Brightmoorllc. The existing website is dated and built in wordpress. The new website will not be wordpress. The project folder includes an overview.txt file with details on the project. The file also contains a list of websites that he/she likes which I am sure is very helpful .
Number of Pages Required
1 page

```html
<!DOCTYPE html>
<html lang="en">
<head>
<meta charset="utf-8">
<title>Brightmoor LLC</title>
<link href="https://fonts.googleapis.com/css2?family=Questrial&family=Barlow:ital,wght@0,400;0,500;0,600;1,400&display=swap" rel="stylesheet">
<style>
:root{
  --blue:#1a73c9;
  --blue-deep:#0d5aa6;
  --blue-bright:#1e88e5;
  --ink:#222a33;
  --text:#4a525b;
  --muted:#7a828a;
  --pale:#eaf2f9;
  --line:#d9dde2;
  --orange:#f57c12;
  --white:#ffffff;
  --photo-top:#4f8fd2;
  --photo-bottom:#2a62a0;
}
*{box-sizing:border-box;margin:0;padding:0}
html,body{width:1200px;height:4098px;overflow:hidden;background:var(--white)}
body{position:relative;font-family:"Barlow",sans-serif;color:var(--text)}
.abs{position:absolute}
.heading{font-family:"Questrial",sans-serif;color:var(--ink)}
.rule{display:block;width:70px;height:3px;background:var(--blue);margin:10px auto 0}

/* header */
.site-header{left:0;top:0;width:1200px;height:90px;background:var(--white)}
.brand{display:flex;align-items:center;gap:12px;font-family:"Questrial",sans-serif;font-size:32px;color:var(--blue)}
.brand-dot{width:56px;height:56px;border-radius:50%;background:var(--blue)}
.site-header .brand{position:absolute;left:80px;top:17px}
.nav{position:absolute;left:349px;top:36px;display:flex;gap:32px;font-family:"Questrial",sans-serif;font-size:15px;color:var(--ink)}
.nav .active{color:var(--blue);border-bottom:2px solid var(--blue);padding-bottom:14px}
.phone-tab{position:absolute;right:0;top:0;width:212px;height:90px;background:var(--blue-bright);clip-path:polygon(22px 0,100% 0,100% 100%,0 100%);color:var(--white);font-family:"Questrial",sans-serif;font-size:16px;font-weight:600;display:flex;align-items:center;gap:8px;padding-left:40px}

/* hero */
.hero{left:0;top:90px;width:1200px;height:660px;overflow:hidden}
.hero-photo{position:absolute;inset:0;background:linear-gradient(180deg,var(--photo-top) 0%,var(--photo-bottom) 100%)}
.hero-copy{position:absolute;left:112px;top:176px;color:var(--white)}
.hero-copy h1{font-family:"Questrial",sans-serif;font-weight:400;font-size:38px;line-height:46px}
.hero-copy h1 b{font-weight:700;-webkit-text-stroke:.6px #fff}
.hero-copy p{font-size:18px;line-height:25px;margin-top:14px;width:430px}
.btn-outline-light{display:inline-block;margin-top:22px;border:2px solid var(--white);padding:13px 38px;font-family:"Questrial",sans-serif;font-weight:600;font-size:15px;color:var(--white)}
.hero-arrow{position:absolute;top:240px}
.hero-wave{position:absolute;left:0;bottom:0}

/* about */
.about-photo{left:116px;top:787px;width:436px;height:436px}
.about-copy{left:592px;top:826px;width:490px}
.eyebrow{font-family:"Questrial",sans-serif;font-size:16px;color:var(--blue)}
.about-copy h2{font-size:34px;line-height:38px;font-weight:700;margin-top:6px;letter-spacing:-.3px}
.about-copy .rule{margin:8px 0 0 46px;width:40px;height:2px}
.about-copy p{font-size:16px;line-height:27px;margin-top:16px}
.btn-outline{display:inline-block;border:2px solid var(--blue);color:var(--blue);font-family:"Questrial",sans-serif;font-weight:600;font-size:13px;padding:14px 33px;margin-top:30px}

/* services */
.services{left:0;top:1270px;width:1200px;height:850px}
.services-bg{position:absolute;inset:0}
.services h2{position:absolute;left:0;width:1200px;top:100px;text-align:center;font-size:28px;letter-spacing:2px}
.service-card{position:absolute;width:312px;height:188px;border:1px solid #9bbbd8;background:rgba(255,255,255,.35);text-align:center;padding-top:52px}
.service-icon{position:absolute;left:113px;top:-44px;width:86px;height:86px;border-radius:50%;border:4px solid var(--blue);background:var(--white)}
.service-card h3{font-family:"Questrial",sans-serif;font-size:16px;font-weight:600;color:var(--ink)}
.service-card p{font-size:13px;line-height:19px;color:var(--muted);width:250px;margin:8px auto 0}
.btn-small{display:inline-block;margin-top:12px;border:2px solid var(--blue);color:var(--blue);font-size:10px;font-weight:600;padding:7px 22px}
.btn-solid{position:absolute;left:473px;top:709px;width:221px;height:51px;background:var(--blue);color:var(--white);font-family:"Questrial",sans-serif;font-weight:600;font-size:15px;display:flex;align-items:center;justify-content:center}

/* gallery */
.gallery-title{left:0;top:2202px;width:1200px;text-align:center;font-size:28px;letter-spacing:1px}
.compare{top:2301px;width:479px;height:305px;display:flex}
.compare .half{flex:1}
.compare .split{width:2px;background:var(--white)}
.compare-handle{position:absolute;top:129px;width:50px;height:50px;border-radius:50%;border:3px solid var(--white);display:flex;align-items:center;justify-content:center}

/* testimonials */
.testimonials{left:0;top:2711px;width:1200px;height:555px}
.testimonials-bg{position:absolute;inset:0}
.testimonials h2{position:absolute;left:0;width:1200px;top:80px;text-align:center;font-size:36px;color:var(--white)}
.testimonials .rule{background:var(--white)}
.quote-card{position:absolute;left:296px;top:190px;width:602px;height:230px;background:var(--white);border-radius:0 90px 0 90px;text-align:center;padding-top:56px}
.quote-card blockquote{font-style:italic;font-size:18px;line-height:23px;color:var(--ink);width:500px;margin:0 auto}
.quote-card cite{display:block;font-style:normal;font-family:"Questrial",sans-serif;font-weight:600;font-size:14px;color:var(--ink);margin-top:18px}
.quote-card small{display:block;font-size:13px;color:var(--ink);margin-top:6px}
.quote-mark{position:absolute;left:572px;top:162px;width:54px;height:54px;border-radius:50%;background:#8fc1ee;color:var(--white);font-family:"Questrial",sans-serif;font-size:38px;line-height:62px;text-align:center}

/* contact */
.contact{left:0;top:3266px;width:1200px;height:461px}
.contact-bg{position:absolute;inset:0;background:linear-gradient(180deg,#ffffff 0%,#f1f6fa 45%,#d9e6ee 100%)}
.contact h2{position:absolute;left:0;width:1200px;top:60px;text-align:center;font-size:36px}
.field{position:absolute;background:var(--white);border:1px solid #c9ced3;display:flex;align-items:center;gap:10px;padding-left:16px;font-size:13px;color:var(--ink)}
.field.message{align-items:flex-start;padding-top:12px}
.btn-send{position:absolute;left:520px;top:324px;width:172px;height:47px;border-radius:24px;background:var(--orange);color:var(--white);font-family:"Questrial",sans-serif;font-weight:600;font-size:14px;display:flex;align-items:center;justify-content:center}

/* footer */
.footer .brand{position:absolute;left:127px;top:3785px;font-size:32px}
.footer-about{left:133px;top:3860px;width:300px;font-size:12px;line-height:19px;color:var(--muted)}
.social{left:133px;top:3936px;display:flex;gap:12px}
.social span{width:29px;height:29px;border-radius:50%;background:var(--blue)}
.footer-col{top:3790px}
.footer-col h4{font-family:"Questrial",sans-serif;font-size:18px;font-weight:600;color:var(--ink);border-left:3px solid var(--blue);padding-left:18px;margin-left:-21px}
.links{display:grid;grid-template-columns:136px 120px;row-gap:13px;margin-top:20px;font-size:14px;color:var(--text)}
.contact-list{margin-top:14px;font-size:13px;color:var(--text)}
.contact-list li{list-style:none;display:flex;gap:14px;margin-bottom:14px;line-height:21px}
.footer-line{left:116px;top:4043px;width:968px;height:1px;background:var(--line)}
.copyright{left:0;top:4060px;width:1200px;text-align:center;font-size:11px;color:var(--muted)}
.vdivider{width:1px;height:160px;background:var(--line)}
</style>
</head>
<body>

<header class="abs site-header">
  <div class="brand"><span class="brand-dot"></span>Brightmoor</div>
  <nav class="nav">
    <span class="active">Services</span><span>About Us</span><span>FAQs</span><span>Employment</span><span>Testimonials</span><span>Gallery</span><span>Contact Us</span>
  </nav>
  <div class="phone-tab">
    <svg width="18" height="18" viewBox="0 0 24 24" fill="none" stroke="#fff" stroke-width="2"><path d="M5 3h4l2 5-2.5 1.5a11 11 0 0 0 6 6L16 13l5 2v4a2 2 0 0 1-2 2A16 16 0 0 1 3 5a2 2 0 0 1 2-2z"/></svg>
    (555) 010 4477
  </div>
</header>

<section class="abs hero">
  <div class="hero-photo" role="img" aria-label="Calm lake with pine-lined shore under a blue sky"></div>
  <div class="hero-copy">
    <h1>WE KNOW THERE IS<br><b>NO LIFE LIKE THE LAKE LIFE</b></h1>
    <p>Brightmoor LLC is a company formed in response to the increasing incidence of invasive species</p>
    <span class="btn-outline-light">FREE ESTIMATE</span>
  </div>
  <svg class="hero-arrow" style="left:24px" width="30" height="56" viewBox="0 0 30 56"><path d="M26 4 4 28l22 24" fill="none" stroke="#fff" stroke-width="3"/></svg>
  <svg class="hero-arrow" style="right:24px" width="30" height="56" viewBox="0 0 30 56"><path d="M4 4l22 24L4 52" fill="none" stroke="#fff" stroke-width="3"/></svg>
  <svg class="hero-wave" width="1200" height="120" viewBox="0 0 1200 120">
    <path d="M0 44C200 80 420 110 600 100S980 60 1200 0V120H0Z" fill="#fff"/>
    <path d="M0 40C200 76 420 106 600 96" fill="none" stroke="#1a73c9" stroke-width="4"/>
    <path d="M600 106C800 100 1000 70 1200 8" fill="none" stroke="#0d5aa6" stroke-width="5"/>
    <circle cx="597" cy="58" r="30" fill="#1a73c9" stroke="#fff" stroke-width="4"/>
  </svg>
</section>

<section>
  <svg class="abs about-photo" viewBox="0 0 436 436">
    <circle cx="218" cy="218" r="216" fill="none" stroke="#1a73c9" stroke-width="5"/>
    <path d="M40 360A214 214 0 0 0 360 400" fill="none" stroke="#1a73c9" stroke-width="14"/>
    <defs><linearGradient id="aboutFill" x1="0" y1="0" x2="0" y2="1"><stop offset="0" stop-color="#5a97d6"/><stop offset="1" stop-color="#2f68a3"/></linearGradient></defs>
    <circle cx="210" cy="210" r="206" fill="url(#aboutFill)" role="img" aria-label="Pontoon boats moored at a lake dock"/>
  </svg>
  <div class="abs about-copy">
    <div class="eyebrow">ABOUT US</div>
    <h2 class="heading">AQUATIC INNOVATORS,<br>AT YOUR SERVICE.</h2>
    <span class="rule"></span>
    <p>Brightmoor LLC is a company formed in response to the increasing incidence of invasive species in Minnesota’s lakes and water systems. The impact of these fast-growing nuisances, inspired our venture to effectively control unwanted lake weeds. Brightmoor, LLC helps provide the enjoyable weed-free lake environment craved by water enthusiasts.</p>
    <span class="btn-outline">LEARN MORE</span>
  </div>
</section>

<section class="abs services">
  <svg class="services-bg" width="1200" height="850" viewBox="0 0 1200 850">
    <defs><linearGradient id="svcFill" x1="0" y1="0" x2="0" y2="1"><stop offset="0" stop-color="#f3f7fb"/><stop offset=".6" stop-color="#e6eff6"/><stop offset="1" stop-color="#d6e4ee"/></linearGradient></defs>
    <path d="M0 20C300 0 700 60 1200 10V790C900 850 500 770 0 820Z" fill="url(#svcFill)"/>
    <path d="M145 6C400 -8 700 50 1000 50" fill="none" stroke="#0d5aa6" stroke-width="4"/>
  </svg>
  <h2 class="heading">DOCK INSTALL AND REMOVAL SERVICES<span class="rule"></span></h2>

  <div class="service-card" style="left:106px;top:235px"><span class="service-icon"></span><h3>Canopy Services</h3><p>Lorem Ipsum is simply dummy text of the printing and type setting industry</p><span class="btn-small">LEARN MORE</span></div>
  <div class="service-card" style="left:437px;top:235px"><span class="service-icon"></span><h3>Barge Services (Fall 2022)</h3><p>Lorem Ipsum is simply dummy text of the printing and type setting</p><span class="btn-small">LEARN MORE</span></div>
  <div class="service-card" style="left:772px;top:235px"><span class="service-icon"></span><h3>Dock Lift Services (Fall 2022)</h3><p>Lorem Ipsum is simply dummy text of the printing and type setting</p><span class="btn-small">LEARN MORE</span></div>
  <div class="service-card" style="left:103px;top:477px"><span class="service-icon"></span><h3>Aquatic Weed Removal</h3><p>Lorem Ipsum is simply dummy text of the printing and type setting</p><span class="btn-small">LEARN MORE</span></div>
  <div class="service-card" style="left:434px;top:477px"><span class="service-icon"></span><h3>Beach Clean Up Services</h3><p>Lorem Ipsum is simply dummy text of the printing and type setting</p><span class="btn-small">LEARN MORE</span></div>
  <div class="service-card" style="left:769px;top:477px"><span class="service-icon"></span><h3>Water Trampoline Service</h3><p>Lorem Ipsum is simply dummy text of the printing and type setting</p><span class="btn-small">LEARN MORE</span></div>

  <span class="btn-solid">VIEW MORE SERVICES</span>
</section>

<section>
  <h2 class="abs heading gallery-title">BEFORE &amp; AFTER GALLERY<span class="rule"></span></h2>
  <div class="abs compare" style="left:107px">
    <div class="half" style="background:linear-gradient(180deg,#8a9a78,#7d8066)" role="img" aria-label="Dock covered in lake weeds before cleanup"></div>
    <div class="split"></div>
    <div class="half" style="background:linear-gradient(180deg,#7f9468,#8d8a78)" role="img" aria-label="Same dock after weed removal"></div>
    <span class="compare-handle" style="left:214px"><svg width="22" height="14" viewBox="0 0 22 14"><path d="M8 1 2 7l6 6M14 1l6 6-6 6" fill="#fff"/></svg></span>
  </div>
  <div class="abs compare" style="left:611px">
    <div class="half" style="background:linear-gradient(180deg,#8a8460,#7e7858)" role="img" aria-label="Murky weedy shoreline before cleanup"></div>
    <div class="split"></div>
    <div class="half" style="background:linear-gradient(180deg,#7c8a70,#6f7f6c)" role="img" aria-label="Clear shoreline water after cleanup"></div>
    <span class="compare-handle" style="left:211px"><svg width="22" height="14" viewBox="0 0 22 14"><path d="M8 1 2 7l6 6M14 1l6 6-6 6" fill="#fff"/></svg></span>
  </div>
</section>

<section class="abs testimonials">
  <svg class="testimonials-bg" width="1200" height="555" viewBox="0 0 1200 555">
    <defs><linearGradient id="tFill" x1="0" y1="0" x2="0" y2="1"><stop offset="0" stop-color="#1f8ae6"/><stop offset="1" stop-color="#1670c8"/></linearGradient></defs>
    <path d="M0 0H1200V470C900 560 400 560 0 520Z" fill="url(#tFill)" role="img" aria-label="Blue-tinted lakeside forest backdrop"/>
    <path d="M0 530C400 570 900 560 1200 480" fill="none" stroke="#0d5aa6" stroke-width="6"/>
  </svg>
  <h2 class="heading">TESTIMONIALS<span class="rule"></span></h2>
  <div class="quote-card">
    <blockquote>Everyone used to jump off the water trampoline and instantly get tangled in lake weeds. We contacted Brightmoor and their SCUBA divers have now been solving our problem for the past 4 years!”</blockquote>
    <cite>Willow Point Shore Association</cite>
    <small>(Lake Harrowmere)</small>
  </div>
  <span class="quote-mark">“</span>
  <svg class="abs" style="left:196px;top:280px" width="24" height="44" viewBox="0 0 24 44"><path d="M21 3 3 22l18 19" fill="none" stroke="#fff" stroke-width="3"/></svg>
  <svg class="abs" style="left:954px;top:280px" width="24" height="44" viewBox="0 0 24 44"><path d="M3 3l18 19L3 41" fill="none" stroke="#fff" stroke-width="3"/></svg>
</section>

<section class="abs contact">
  <div class="contact-bg" role="img" aria-label="Soft lake water backdrop"></div>
  <h2 class="heading">CONTACT US<span class="rule"></span></h2>
  <div class="field" style="left:174px;top:146px;width:421px;height:46px"><svg width="14" height="14" viewBox="0 0 14 14" fill="#9aa1a8"><circle cx="7" cy="4" r="3"/><path d="M1 14a6 6 0 0 1 12 0Z"/></svg>Your Name</div>
  <div class="field" style="left:174px;top:201px;width:421px;height:46px"><svg width="14" height="14" viewBox="0 0 24 24" fill="#9aa1a8"><path d="M5 3h4l2 5-2.5 1.5a11 11 0 0 0 6 6L16 13l5 2v4a2 2 0 0 1-2 2A16 16 0 0 1 3 5a2 2 0 0 1 2-2z"/></svg>Phone number</div>
  <div class="field" style="left:174px;top:256px;width:421px;height:46px"><svg width="15" height="11" viewBox="0 0 15 11" fill="none" stroke="#9aa1a8" stroke-width="1.4"><rect x="1" y="1" width="13" height="9"/><path d="m1 1 6.5 5L14 1"/></svg>Email address</div>
  <div class="field message" style="left:606px;top:146px;width:422px;height:156px">Message</div>
  <span class="btn-send">SEND ENQUIRY</span>
</section>

<footer class="footer">
  <div class="brand"><span class="brand-dot"></span>Brightmoor</div>
  <p class="abs footer-about">Brightmoor LLC is a company formed in response to the increasing incidence of invasive species in Minnesota’s lakes and water systems.</p>
  <div class="abs social"><span></span><span></span><span></span><span></span></div>
  <span class="abs vdivider" style="left:505px;top:3775px"></span>
  <div class="abs footer-col" style="left:529px">
    <h4>QUICK LINKS</h4>
    <div class="links"><span>Home</span><span>FAQs</span><span>Services</span><span>Employment</span><span>About Us</span><span>Testimonials</span><span>Contact Us</span><span>Gallery</span></div>
  </div>
  <span class="abs vdivider" style="left:852px;top:3775px"></span>
  <div class="abs footer-col" style="left:877px">
    <h4>CONTACT US</h4>
    <ul class="contact-list">
      <li><svg width="14" height="20" viewBox="0 0 14 20"><path d="M7 0a7 7 0 0 0-7 7c0 5 7 13 7 13s7-8 7-13a7 7 0 0 0-7-7z" fill="#1a73c9"/><circle cx="7" cy="7" r="2.5" fill="#fff"/></svg><span>418 Birchwood Lane<br>Northvale, MN 55000</span></li>
      <li><svg width="15" height="20" viewBox="0 0 15 20" fill="none" stroke="#1a73c9" stroke-width="1.4"><rect x="1" y="5" width="13" height="9"/><path d="m1 5 6.5 5L14 5"/></svg><span>enquiry@brightmoor.example</span></li>
      <li><svg width="15" height="20" viewBox="0 0 24 24" fill="#1a73c9"><path d="M5 3h4l2 5-2.5 1.5a11 11 0 0 0 6 6L16 13l5 2v4a2 2 0 0 1-2 2A16 16 0 0 1 3 5a2 2 0 0 1 2-2z"/></svg><span style="font-size:15px">(555) 014-2290</span></li>
    </ul>
  </div>
  <div class="abs footer-line"></div>
  <p class="abs copyright">Copyright: 2022 Brightmoor LLC</p>
</footer>

</body>
</html>
```